Ward Compass Business Card Design*

We need a business card design for our company Ward Compass. Our company is specialized in providing online consulting services regarding medical institutions, hospitals and doctors. We work with patients worldwide looking to choose between healthcare providers. We have a website you may use as a reference, where we list doctors and clinics worldwide. So we target Medical providers as well as patients worldwide.
Target Market(s)
Medical Providers and patients around the world
Industry/Entity Type
Medical
Contact Information for Business Card
Salwa Kettani
CEO
+90 612 348 2175
info@wardcompass.example
www.wardcompass.example
14 Annakhil 7 H.R.B. Rabat, Morocco
Requirements
Must have
- Company logo/name on one full side, personal info and smaller logo and company name on the other side.
Nice to have
- Smart and elegant design

```html
<!DOCTYPE html>
<html lang="en">
<head>
<meta charset="utf-8">
<title>Ward Compass — Business Card</title>
<link rel="stylesheet" href="https://fonts.googleapis.com/css2?family=Nunito+Sans:wght@400;700;800&display=swap">
<style>
  :root {
    --navy: #1a4574;
    --paper: #f3f3f5;
    --grey: #7f7d7f;
    --ink: #3a3a3c;
    --white: #ffffff;
    --backdrop: #e8e4de;
  }
  * { box-sizing: border-box; margin: 0; padding: 0; }
  html, body {
    width: 900px; height: 1200px; overflow: hidden;
    background: var(--backdrop);
    font-family: "Nunito Sans", "Helvetica Neue", Arial, sans-serif;
  }
  .canvas { position: relative; width: 900px; height: 1200px; }
  .card {
    position: absolute; left: 77px; width: 746px; height: 436px;
    box-shadow: 0 3px 8px rgba(0,0,0,0.25);
  }
  .card-front { top: 134px; background: var(--navy); }
  .card-back { top: 638px; background: var(--paper); }

  .front-brand {
    position: absolute; left: 128px; top: 174px; height: 90px;
    display: flex; align-items: center; gap: 26px;
  }
  .brand-dot { width: 86px; height: 86px; border-radius: 50%; background: var(--grey); }
  .front-name {
    font-weight: 800; font-size: 46px; letter-spacing: 0.5px;
    color: var(--white); white-space: nowrap;
  }

  .back-brand {
    position: absolute; left: 146px; top: 146px; width: 210px;
    display: flex; flex-direction: column; align-items: center; gap: 16px;
  }
  .back-brand .brand-dot { width: 84px; height: 84px; background: var(--navy); }
  .back-name {
    font-weight: 800; font-size: 20px; letter-spacing: 0.6px;
    color: var(--navy); white-space: nowrap;
  }

  .divider {
    position: absolute; left: 382px; top: 151px; width: 1px; height: 131px;
    background: var(--ink);
  }
  .details { position: absolute; left: 424px; top: 150px; color: var(--ink); }
  .person-name { font-size: 26px; line-height: 32px; font-weight: 400; white-space: nowrap; }
  .person-name .given { font-weight: 800; color: var(--navy); }
  .person-role { font-size: 18px; line-height: 22px; margin-top: 0; }
  .contact-list { list-style: none; margin-top: 10px; }
  .contact-item {
    display: flex; align-items: center; gap: 10px;
    font-size: 17px; line-height: 26px; white-space: nowrap;
  }
  .contact-icon { width: 19px; height: 19px; flex: none; }
  .website { margin-top: 6px; font-size: 17px; color: var(--navy); }
</style>
</head>
<body>
<main class="canvas">
  <section class="card card-front" aria-label="Card front">
    <div class="front-brand">
      <span class="brand-dot"></span>
      <span class="front-name">WARD COMPASS</span>
    </div>
  </section>

  <section class="card card-back" aria-label="Card back">
    <div class="back-brand">
      <span class="brand-dot"></span>
      <span class="back-name">WARD COMPASS</span>
    </div>
    <div class="divider"></div>
    <div class="details">
      <p class="person-name"><span class="given">SALWA</span> KETTANI</p>
      <p class="person-role">CEO</p>
      <ul class="contact-list">
        <li class="contact-item">
          <svg class="contact-icon" viewBox="0 0 20 20" aria-hidden="true">
            <circle cx="10" cy="10" r="10" fill="#1a4574"/>
            <path d="M7 5.2c.5-.3 1 0 1.2.4l.7 1.6c.2.4 0 .8-.3 1l-.6.5c.5 1.1 1.3 2 2.4 2.6l.5-.6c.3-.3.7-.4 1-.2l1.6.8c.4.2.6.7.3 1.1-.6 1-1.6 1.4-2.6 1-2.6-1-4.5-3-5.4-5.6-.3-1 .2-2 1.2-2.6z" fill="#fff"/>
          </svg>
          <span>+90 612 348 2175</span>
        </li>
        <li class="contact-item">
          <svg class="contact-icon" viewBox="0 0 20 20" aria-hidden="true">
            <circle cx="10" cy="10" r="10" fill="#1a4574"/>
            <rect x="5.5" y="7" width="9" height="6.5" rx="0.6" fill="#fff"/>
            <path d="M5.8 7.4 10 10.6l4.2-3.2" fill="none" stroke="#1a4574" stroke-width="0.9"/>
          </svg>
          <span>info@wardcompass.example</span>
        </li>
      </ul>
      <p class="website">www.wardcompass.example</p>
    </div>
  </section>
</main>
</body>
</html>
```